Company website for an international IT business

We require a website for our business, Korvel Solutions. The business has two primary areas: Lanterns, which includes two machine learning/deep learning based products and IT consultancy, which is the service we provide to other businesses.

We bridge cutting-edge research to market.

STYLING:
The site can be on single page or multi-page. This is fully open to suggestion. So long as the look and feel are consistent. Currently, we have no strong preference for colors, styles or layouts.
You can find the logo of our website in the attachment “Korvel-logo.png” and “Korvel-logo-landscape.png”.

CONTENT:
You can find the text of the website in “Website-Content.pdf”, which explains the services and products of our business. The format of the text is also open to suggestion - including breaking up the text into visually appealing sections.
We would also like to include suitable images on the website so that it does not appear to be a text-heavy page. We are happy to have placeholder images on stock image sites if needed. We are open to suggestions on placing of images

ATTACHMENT:

Industry/Entity Type

It Company

Coding

Coded - Design and coding required

Number of Pages Required

1 page

Colors

Designer to choose colors to be used in the design.

Requirements
Must have
• A full description of the requirement is in the attachment "Website-Content.pdf"
• The design must have HTML/CSS, and all resources relevant (images, fonts etc)
• We are
Nice to have
• We are open to suggestions on top of the requirement, please reach out and communicate.

```html
<!DOCTYPE html>
<html lang="en">
<head>
<meta charset="utf-8">
<title>Korvel Solutions</title>
<link rel="stylesheet" href="https://fonts.googleapis.com/css2?family=Michroma&family=Montserrat:wght@600;700&family=Open+Sans:wght@400;600&display=swap">
<style>
:root{
  --blue:#1487c9;
  --ink:#1b1b1b;
  --grey:#8a8a8a;
  --text:#444;
  --line:#d8d8d8;
  --pale:#efefef;
  --night:#1c2330;
}
*{box-sizing:border-box;margin:0;padding:0}
html,body{width:1200px;height:3651px;overflow:hidden}
body{font-family:"Open Sans",sans-serif;color:var(--text);background:#fff;position:relative}
section,header,footer{position:absolute;left:0;width:1200px}
.heading{font-family:"Michroma",sans-serif;text-transform:uppercase;letter-spacing:1px;font-weight:400}
.img{position:absolute}

/* header */
.site-header{top:0;height:122px;background:#fff}
.brand{position:absolute;left:78px;top:14px;display:flex;align-items:center;gap:14px}
.brand-dot{width:86px;height:86px;border-radius:50%;background:var(--blue)}
.brand-name{font-family:"Montserrat",sans-serif;font-weight:700;font-size:30px;color:var(--ink)}
.contact-bar{position:absolute;top:14px;left:770px;display:flex;gap:40px;font-size:16px;color:var(--grey);align-items:center}
.contact-bar span{display:flex;align-items:center;gap:12px}
.ring{width:40px;height:40px;border:1.5px solid var(--blue);border-radius:50%;display:flex;align-items:center;justify-content:center}
.nav{position:absolute;top:82px;left:430px;display:flex;gap:0;font-size:16px;color:#9a9a9a}
.nav a{color:inherit;text-decoration:none;padding:0 28px 12px;position:relative}
.nav a.active{color:var(--blue)}
.nav a.active::after{content:"";position:absolute;left:16px;right:16px;bottom:0;height:3px;background:var(--blue)}

/* hero */
.hero{top:122px;height:555px;background:linear-gradient(180deg,#2b2a33 0%,#4a3a34 35%,#5c4a3c 50%,#1b1d25 100%);color:#fff;text-align:center}
.hero h1{font-family:"Montserrat",sans-serif;font-weight:700;font-size:70px;margin-top:200px;letter-spacing:1px}
.hero .tagline{font-family:"Montserrat",sans-serif;font-weight:600;font-size:27px;color:#9aa0a8;margin-top:4px;letter-spacing:1px}
.hero p{font-size:16px;width:860px;margin:10px auto 0;line-height:1.5}
.arrow{position:absolute;top:255px}

/* welcome */
.welcome{top:677px;height:479px;text-align:center}
.welcome h2{font-size:38px;color:var(--ink);margin-top:48px}
.welcome h2 b{color:var(--blue);font-weight:400}
.divider{width:460px;margin:18px auto 0;position:relative;height:20px}
.divider::before{content:"";position:absolute;left:0;right:0;top:10px;border-top:1px solid var(--line)}
.divider i{position:absolute;left:220px;top:0;width:20px;height:20px;border-radius:50%;background:#777}
.welcome .intro{width:860px;margin:20px auto 0;font-size:15px;color:#9a9a9a;line-height:1.45}
.services{position:absolute;top:250px;left:0;width:1200px}
.service{position:absolute;width:320px;text-align:center}
.service h3{font-weight:400;font-size:23px;color:var(--blue);margin-top:14px}
.service p{font-size:15px;line-height:1.5;margin-top:8px;color:#555}

/* products */
.product h2{font-size:34px;color:var(--blue)}
.product p{font-size:14.5px;line-height:1.5;margin-top:16px;color:#555}
.halo{top:1156px;height:409px;background:var(--pale)}
.halo .copy{position:absolute;left:574px;top:92px;width:600px}
.kerbside{top:1565px;height:407px;background:#fff}
.kerbside .copy{position:absolute;left:80px;top:96px;width:580px}

/* expertise */
.expertise{top:1972px;height:345px;background:linear-gradient(135deg,#1e3050,#0f1828 60%,#243a5a);color:#fff;text-align:center}
.expertise h2{font-size:37px;margin-top:96px}
.expertise p{font-size:19px;margin-top:20px;color:#e4e7ec;line-height:1.45}

/* help */
.help{top:2317px;height:538px;background:linear-gradient(90deg,#f4f6f8,#e3e8ee 60%,#f0f2f4)}
.help h2{position:absolute;left:110px;top:78px;font-size:35px;color:var(--ink)}
.help-item{position:absolute;left:108px;display:flex;align-items:flex-start;gap:18px;width:560px}
.help-icon{flex:none;width:84px;height:84px;border-radius:50%;background:var(--blue);border:4px solid #fff;box-shadow:0 0 0 1.5px var(--blue)}
.help-icon.alt{background:#fff;box-shadow:0 0 0 1.5px #333}
.help-item h3{font-weight:400;font-size:21px;color:var(--ink);line-height:1.3}
.help-item p{font-size:13px;color:#666;margin-top:6px;line-height:1.45}

/* contact */
.contact{top:2855px;height:480px;background:linear-gradient(180deg,#2a3037,#161a1f);text-align:center}
.contact h2{color:#fff;font-size:37px;margin-top:52px}
.field{position:absolute;background:#fff;border:2px solid #5ab0e0;font-size:13px;color:#888;text-align:left;padding:14px 18px}
.submit{position:absolute;left:117px;top:331px;width:966px;height:52px;border:1.5px solid #fff;color:#fff;font-size:21px;line-height:49px;letter-spacing:1px}

/* footer */
.site-footer{top:3335px;height:316px;background:#fff}
.site-footer h4{font-size:20px;color:var(--blue);position:absolute;top:58px}
.post{position:absolute;left:80px;display:flex;gap:16px;width:300px}
.post .thumb{flex:none;width:54px;height:54px;border-radius:50%}
.post p{font-size:13px;color:#555;line-height:1.4}
.post small{display:block;color:var(--blue);font-size:13px}
.foot-brand{position:absolute;left:0;width:1192px;top:56px;text-align:center}
.foot-brand .brand-dot{margin:0 auto;width:96px;height:96px}
.foot-brand .brand-name{display:block;margin-top:10px;font-size:26px}
.foot-brand small{display:block;margin-top:14px;font-size:14px;color:#444}
.foot-brand small b{color:var(--blue);font-weight:400}
.info{position:absolute;left:813px;display:flex;gap:18px;align-items:flex-start;font-size:13px;color:#666;width:320px;line-height:1.4}
</style>
</head>
<body>

<header class="site-header">
  <div class="brand"><div class="brand-dot"></div><span class="brand-name">KORVEL</span></div>
  <div class="contact-bar">
    <span><i class="ring"><svg width="18" height="18" viewBox="0 0 24 24"><path d="M6.6 10.8a15 15 0 0 0 6.6 6.6l2.2-2.2c.3-.3.7-.4 1-.2 1.1.4 2.3.6 3.6.6.6 0 1 .4 1 1V20c0 .6-.4 1-1 1A17 17 0 0 1 3 4c0-.6.4-1 1-1h3.5c.6 0 1 .4 1 1 0 1.3.2 2.5.6 3.6.1.3 0 .7-.2 1z" fill="none" stroke="#1487c9" stroke-width="1.6"/></svg></i>123 456 7878</span>
    <span><i class="ring"><svg width="18" height="14" viewBox="0 0 18 14"><rect x="1" y="1" width="16" height="12" fill="none" stroke="#1487c9" stroke-width="1.5"/><path d="M1 1l8 7 8-7" fill="none" stroke="#1487c9" stroke-width="1.5"/></svg></i>info@korvel.com</span>
  </div>
  <nav class="nav">
    <a class="active">Home</a><a>About Us</a><a>Lanterns</a><a>Consultancy</a><a>News</a><a>Contact Us</a>
  </nav>
</header>

<section class="hero" role="img" aria-label="Night skyline of a city at dusk">
  <h1>KORVEL SOLUTIONS</h1>
  <div class="tagline">Business Coaching &amp; Consulating For IT</div>
  <p>Lorem Ipsum is simply dummy text of the printing and typesetting industry. Lorem Ipsum has been the industry's standard dummy text ever since the 1500s, when an unknown printer took a galley of type.</p>
  <svg class="arrow" style="left:24px" width="22" height="44" viewBox="0 0 22 44"><path d="M20 2L2 22l18 20" fill="none" stroke="#fff" stroke-width="2"/></svg>
  <svg class="arrow" style="left:1156px" width="22" height="44" viewBox="0 0 22 44"><path d="M2 2l18 20L2 42" fill="none" stroke="#fff" stroke-width="2"/></svg>
</section>

<section class="welcome">
  <h2 class="heading">Welcome to <b>Korvel</b></h2>
  <div class="divider"><i></i></div>
  <p class="intro">Lorem Ipsum is simply dummy text of the printing and typesetting industry. Lorem Ipsum has been the industry's standard dummy text ever since the 1500s, when an unknown printer took a galley of type and scrambled it to make a type specimen book. It has survived not only five centuries, but also the leap into electronic typesetting.</p>
  <div class="services">
    <div class="service" style="left:96px">
      <svg width="80" height="60" viewBox="0 0 80 60"><rect x="2" y="2" width="76" height="56" fill="none" stroke="#333" stroke-width="3"/><line x1="2" y1="14" x2="78" y2="14" stroke="#333" stroke-width="3"/><path d="M30 28l-8 8 8 8M50 28l8 8-8 8M44 26l-8 20" fill="none" stroke="#333" stroke-width="3"/></svg>
      <h3>Software Development</h3>
      <p>Lorem Ipsum is simply dummy text of<br>the printing and typesetting.</p>
    </div>
    <div class="service" style="left:436px">
      <svg width="80" height="60" viewBox="0 0 80 60"><circle cx="40" cy="30" r="14" fill="#1487c9"/><g fill="#555"><circle cx="14" cy="12" r="4"/><circle cx="66" cy="12" r="4"/><circle cx="10" cy="40" r="4"/><circle cx="70" cy="42" r="4"/><circle cx="40" cy="4" r="3"/><circle cx="40" cy="56" r="3"/><circle cx="24" cy="52" r="3"/><circle cx="58" cy="54" r="3"/></g></svg>
      <h3>IOT System Design</h3>
      <p>Lorem Ipsum is simply dummy text of<br>the printing and typesetting industry.</p>
    </div>
    <div class="service" style="left:784px">
      <svg width="80" height="60" viewBox="0 0 80 60"><path d="M28 58V44c-8-4-12-12-10-20 3-12 18-18 28-12 8 4 10 12 8 18l4 6h-6v6h-8v6z" fill="#333"/><circle cx="54" cy="14" r="8" fill="#1487c9"/><circle cx="64" cy="26" r="5" fill="#1487c9"/></svg>
      <h3>Machine learning solutions</h3>
      <p>Lorem Ipsum is simply dummy text of<br>the printing and typesetting.</p>
    </div>
  </div>
</section>

<section class="product halo">
  <div class="img" role="img" aria-label="Black and white photo of a driver holding a phone at the wheel" style="left:0;top:36px;width:548px;height:373px;background:linear-gradient(120deg,#e9e9e9,#9a9a9a 45%,#3c3c3c 80%,#d0d0d0)"></div>
  <div class="copy">
    <h2 class="heading">Halo</h2>
    <p>The primary cause of accidents on the road are caused by human error. Of these driver distraction and fatigue are the real problem.</p>
    <p>Halo is a system for HGV/HMT drivers to make every journey safer – safer for the driver and safer to other road users.</p>
    <p>Halo uses advanced deep learning techniques to monitor driver behavior in real time inside the cabin. Halo can detect driver distraction (mobile phone usage, smoking, failure tofocused on the road ahead) and also monitor for classic signs of fatigue.</p>
  </div>
</section>

<section class="product kerbside">
  <div class="img" role="img" aria-label="Black and white photo of hands signing a document with a pen" style="left:730px;top:0;width:470px;height:407px;background:linear-gradient(135deg,#fff 0%,#bdbdbd 35%,#4a4a4a 70%,#a8a8a8)"></div>
  <div class="copy">
    <h2 class="heading">Kerbside</h2>
    <p>Kerbside is a machine learning system that tracks and analyzes live used car trading markets. It learns every aspect of a car ads, through which, it creates powerful market intelligence for all parties in the used car ecosystem:</p>
    <p>It gives inexperienced buyers independent market consensus price, depreciation and approximated running costs for cars they are interested.</p>
    <p>It provides dealerships comprehensive market intelligence including demands, supply, consensus price, and expected market life of car</p>
  </div>
</section>

<section class="expertise" role="img" aria-label="Dark blue photo of a laptop and charts on a desk">
  <h2 class="heading">Strong Expertise</h2>
  <p>We have many years experience in machine learning, data mining, app<br>development, DevOps and hardware design.</p>
  <p style="margin-top:14px">We solve "hard" problems for business</p>
</section>

<section class="help">
  <div class="img" role="img" aria-label="Businessman in a suit beside rising growth arrows" style="left:640px;top:110px;width:520px;height:428px;background:linear-gradient(90deg,rgba(220,226,234,0),#9fb0c4 40%,#2d3a52 60%,#b5c4d6)"></div>
  <h2 class="heading">How we can help</h2>
  <div class="help-item" style="top:142px"><i class="help-icon"></i><div><h3>Acquire more development capacity and get result fast</h3><p>Lorem Ipsum is simply dummy text of the printing and<br>typesetting.</p></div></div>
  <div class="help-item" style="top:272px"><i class="help-icon alt"></i><div><h3 style="margin-top:8px">Avoid the overhead incurred by frequent scaling of your development team</h3></div></div>
  <div class="help-item" style="top:398px"><i class="help-icon alt"></i><div><h3 style="margin-top:28px">Reach a wide spectrum of expertise</h3></div></div>
</section>

<section class="contact" role="img" aria-label="Dark photo of a laptop on a desk">
  <h2 class="heading">Contact Us</h2>
  <div class="field" style="left:117px;top:139px;width:331px;height:52px">Name</div>
  <div class="field" style="left:117px;top:200px;width:331px;height:52px">E - Mail</div>
  <div class="field" style="left:117px;top:263px;width:331px;height:52px">Phone</div>
  <div class="field" style="left:460px;top:139px;width:623px;height:176px">Message</div>
  <div class="submit">SUBMIT</div>
</section>

<footer class="site-footer">
  <h4 class="heading" style="left:80px">Blog</h4>
  <div class="post" style="top:108px"><i class="thumb" role="img" aria-label="City at sunset" style="background:linear-gradient(#e08a3a,#2b2f45)"></i><p>Lorem Ipsum is simply dummy<br>text of the printing.<small>Today 5:60 pm - 15.01.2018</small></p></div>
  <div class="post" style="top:174px"><i class="thumb" role="img" aria-label="Portrait photo" style="background:linear-gradient(#c9ced6,#3a4356)"></i><p>Lorem Ipsum is simply dummy<br>text of the printing.<small>Today 2:10 pm - 13.01.2018</small></p></div>

  <div class="foot-brand"><div class="brand-dot"></div><span class="brand-name">KORVEL</span><small>© <b>KORVEL</b> – 2018. All Rights Reserved</small></div>

  <h4 class="heading" style="left:813px">Contact Info</h4>
  <div class="info" style="top:100px"><svg width="18" height="24" viewBox="0 0 18 24"><path d="M9 1a8 8 0 0 0-8 8c0 6 8 14 8 14s8-8 8-14a8 8 0 0 0-8-8z" fill="none" stroke="#555" stroke-width="1.5"/><circle cx="9" cy="9" r="3" fill="none" stroke="#555" stroke-width="1.5"/></svg><span>PO Box 1234, Street Name, City Name,<br>Country 123456.</span></div>
  <div class="info" style="top:160px"><svg width="18" height="18" viewBox="0 0 24 24"><path d="M6.6 10.8a15 15 0 0 0 6.6 6.6l2.2-2.2c.3-.3.7-.4 1-.2 1.1.4 2.3.6 3.6.6.6 0 1 .4 1 1V20c0 .6-.4 1-1 1A17 17 0 0 1 3 4c0-.6.4-1 1-1h3.5c.6 0 1 .4 1 1 0 1.3.2 2.5.6 3.6.1.3 0 .7-.2 1z" fill="none" stroke="#555" stroke-width="1.8"/></svg><span>123 4567 890</span></div>
  <div class="info" style="top:204px"><svg width="18" height="14" viewBox="0 0 18 14"><rect x="1" y="1" width="16" height="12" fill="none" stroke="#555" stroke-width="1.5"/><path d="M1 1l8 7 8-7" fill="none" stroke="#555" stroke-width="1.5"/></svg><span>info@korvel.com</span></div>
</footer>

</body>
</html>
```